Korvath Supply Website Redesign

Currently korvathsupply.example is focussed on fulfillment and transport from various products in the BBQ segment. However, no we want to update our business activities to Product Development, Brand Development, Online Positioning, Logistics & Aftersales, and Promotional BBQs. We will be a business for Outdoor Leisure Development from A to Z.

Therefore, we need a brand new website. The colours of the current website may be the same. However, i'd like to keep it clean. More white and use blue and green as accent colours. It is a business to business organization so the website should be looking formal and corporate. However we sell fun products so not too formal and corporate.

Pages we need; Home, About, Contact, Our Services (+ page per service) a place to share our news/blogs.

I have added some sort of mock up of an idea. However it needs some finetuning.

Target Market(s)

Businesses

Industry/Entity Type

Corporate/Logistics/Marketing

Coding

Coded - Design and coding required

Colors

Designer to choose colors to be used in the design.

Requirements
Must have
• Show clear distinguishing of the different services we provide (Product Development, Brand Development, Online Positioning, Logistics & Aftersales and Promotional BBQs). Every service should have its own page too. Besides, I would like to have a blog page to share relevant content.
Nice to have
• Show that we are the expert in Outdoor LEisure Development from A to Z
Should not have
• Be too informal. It may be semi-formal

```html
<!DOCTYPE html>
<html lang="en">
<head>
<meta charset="utf-8">
<title>Korvath Supply</title>
<link rel="stylesheet" href="https://fonts.googleapis.com/css2?family=Arimo:wght@400;700&family=Montserrat:wght@400;500;600;700&display=swap">
<style>
:root{
  --teal:#325f6c;
  --teal-dark:#2c5664;
  --green:#35a03b;
  --green-light:#dff0dd;
  --ink:#5a5a5a;
  --heading:#333;
  --white:#fff;
}
*{box-sizing:border-box;margin:0;padding:0}
html,body{width:1200px;height:3595px;overflow:hidden}
body{position:relative;background:var(--white);font-family:"Arimo",Arial,sans-serif;color:var(--ink)}
.abs{position:absolute}

/* header */
.site-header{left:0;top:0;width:1200px;height:140px}
.brand{left:112px;top:40px;display:flex;align-items:center;gap:14px;font-family:"Montserrat",sans-serif;font-weight:700;font-size:44px;color:var(--teal);letter-spacing:1px}
.brand-dot{width:40px;height:40px;border-radius:50%;background:var(--teal)}
.main-nav{right:112px;top:62px;display:flex;gap:54px;font-family:"Montserrat",sans-serif;font-weight:500;font-size:14px;color:#333}
.main-nav .active{color:var(--teal)}

/* hero */
.hero{left:0;top:140px;width:1200px;height:653px;background:linear-gradient(100deg,#6b5a52 0%,#9c6a4a 30%,#8d8c90 60%,#ccc0b0 100%)}
.hero-title{left:112px;top:390px;color:var(--white);font-family:"Montserrat",sans-serif;font-weight:600}
.hero-title .l1{font-size:44px;line-height:58px}
.hero-title .l2{font-size:36px;line-height:56px}

/* service cards */
.service{top:742px;width:188px;height:366px;color:var(--white);text-align:center}
.service.teal{background:var(--teal)}
.service.green{background:var(--green)}
.service svg{margin-top:32px}
.service h3{font-family:"Montserrat",sans-serif;font-weight:700;font-size:18px;margin-top:18px;white-space:nowrap}
.service .sub{font-family:"Montserrat",sans-serif;font-weight:400;font-size:14px;margin-top:3px;letter-spacing:.5px;white-space:nowrap}
.service p{font-size:12.5px;line-height:22px;margin:14px 14px 0;height:88px}
.service .btn{display:inline-block;margin-top:10px;border:2px solid var(--white);border-radius:24px;padding:11px 14px;font-family:"Montserrat",sans-serif;font-weight:600;font-size:13px}

/* welcome */
.welcome{left:112px;top:1206px;width:425px}
.welcome .pre{font-family:"Montserrat",sans-serif;font-weight:500;font-size:24px;color:var(--teal)}
.welcome h2{font-family:"Montserrat",sans-serif;font-weight:600;font-size:40px;color:var(--green);margin-top:8px}
.welcome p{font-size:13.6px;line-height:25.7px;margin-top:22px;text-align:justify}
.btn-solid{display:inline-block;margin-top:28px;background:var(--teal);color:var(--white);border-radius:32px;width:182px;height:60px;line-height:60px;text-align:center;font-family:"Montserrat",sans-serif;font-weight:500;font-size:18px}
.accent-disc{left:773px;top:1176px;width:316px;height:316px;border-radius:50%;background:var(--green-light)}
.photo-disc{left:596px;top:1238px;width:446px;height:446px;border-radius:50%;background:radial-gradient(circle at 45% 40%,#f0a84a,#b65f25 70%,#5a3a2a)}

/* banner */
.banner{left:0;top:1744px;width:1200px;height:561px;background:linear-gradient(180deg,#2f4d84 0%,#3e4f86 45%,#b0673c 78%,#5a3a3c 100%)}
.banner-text{left:668px;top:1810px;width:440px;color:var(--white)}
.banner-text .pre{font-family:"Montserrat",sans-serif;font-weight:500;font-size:24px}
.banner-text h2{font-family:"Montserrat",sans-serif;font-weight:500;font-size:30px;margin-top:6px;white-space:nowrap}
.banner-text p{font-size:13.6px;line-height:25.7px;margin-top:24px;width:425px}
.btn-ghost{display:inline-block;margin-top:30px;border:2px solid var(--white);border-radius:28px;width:240px;height:56px;line-height:52px;text-align:center;font-family:"Montserrat",sans-serif;font-weight:600;font-size:14px}

/* blog */
.blog-title{left:0;top:2352px;width:1200px;text-align:center;font-family:"Montserrat",sans-serif;font-weight:500;font-size:40px;color:var(--teal)}
.blog-title span{color:var(--green)}
.blog-rule{left:574px;top:2412px;width:52px;height:3px;background:var(--teal)}
.post{top:2446px;width:314px}
.post .thumb{width:314px;height:250px}
.post .date{position:absolute;left:16px;top:229px;width:130px;height:40px;line-height:40px;background:var(--green);color:var(--white);text-align:center;font-family:"Montserrat",sans-serif;font-weight:500;font-size:15px}
.post h3{margin-top:48px;font-family:"Montserrat",sans-serif;font-weight:500;font-size:21px;color:var(--heading);white-space:nowrap}
.post p{margin-top:12px;font-size:13.5px;line-height:26px}

/* partners */
.partners{left:0;top:2914px;width:1200px;height:211px;background:var(--green)}
.partner{top:2965px;width:181px;height:108px;border:3px solid var(--white);color:var(--white);display:flex;align-items:center;justify-content:center;font-family:"Montserrat",sans-serif;font-weight:600;font-size:24px}

/* footer */
.site-footer{left:0;top:3125px;width:1200px;height:470px;background:var(--teal)}
.foot-nav{left:0;top:3167px;width:1200px;display:flex;justify-content:center;gap:60px;font-family:"Montserrat",sans-serif;font-weight:600;font-size:14px;color:var(--white)}
.foot-rule{left:112px;top:3216px;width:976px;height:1px;background:rgba(255,255,255,.15)}
.foot-h{top:3250px;font-family:"Montserrat",sans-serif;font-weight:500;font-size:24px;color:var(--white)}
.field{background:var(--white);font-size:11px;color:#444;padding:12px 12px}
.submit{left:110px;top:3456px;width:98px;height:34px;background:var(--green);color:var(--white);font-size:13px;text-align:center;line-height:34px}
.contact-item{left:553px;display:flex;gap:15px;color:var(--white)}
.contact-item .ic{width:44px;height:44px;border-radius:50%;border:2px solid var(--white);display:flex;align-items:center;justify-content:center;flex:none}
.contact-item b{display:block;font-family:"Montserrat",sans-serif;font-weight:500;font-size:17px}
.contact-item span{font-size:13px;line-height:20px}
.foot-brand{left:822px;top:3306px;display:flex;align-items:center;gap:12px;font-family:"Montserrat",sans-serif;font-weight:700;font-size:38px;color:var(--white)}
.foot-brand .dot{width:42px;height:42px;border-radius:50%;background:var(--white)}
.social{top:3396px;width:36px;height:36px;border-radius:50%;border:2px solid var(--white)}
.copyright{left:0;top:3546px;width:1200px;text-align:center;font-family:"Montserrat",sans-serif;font-size:16px;color:var(--white)}
</style>
</head>
<body>

<header class="abs site-header">
  <div class="abs brand"><span class="brand-dot"></span>KORVATH</div>
  <nav class="abs main-nav"><span class="active">HOME</span><span>ABOUT</span><span>CONTACT</span><span>OUR SERVICES</span><span>OUR NEWS</span></nav>
</header>

<section class="abs hero" role="img" aria-label="Photo collage of a cargo plane, shipping containers, trucks and two women working on a laptop"></section>
<h1 class="abs hero-title"><div class="l1">Korvath Supply</div><div class="l2">E Commerce &amp; Order Portals</div></h1>

<div class="abs service teal" style="left:112px">
  <svg width="70" height="74" viewBox="0 0 76 80" fill="none" stroke="#fff" stroke-width="2.5"><rect x="4" y="20" width="68" height="56"/><rect x="14" y="4" width="14" height="50" rx="3"/><path d="M40 32h22v30H40zM40 47h22M51 32v30"/></svg>
  <h3>PRODUCT</h3><div class="sub">DEVELOPMENT</div>
  <p>We believe that the partners we work for should be able to focus on building their brand</p>
  <span class="btn">LEARN MORE</span>
</div>
<div class="abs service green" style="left:309px">
  <svg width="70" height="74" viewBox="0 0 76 80" fill="none" stroke="#fff" stroke-width="2.5"><rect x="4" y="4" width="68" height="72"/><path d="M4 16h68M32 30h32M32 42h32M32 54h32M32 66h32M12 30l12 0 0 40-6 6-6-6z"/></svg>
  <h3>BRAND</h3><div class="sub">DEVELOPMENT</div>
  <p>We can process orders automatically via our portals. Depending on the type</p>
  <span class="btn">LEARN MORE</span>
</div>
<div class="abs service teal" style="left:506px">
  <svg width="78" height="74" viewBox="0 0 84 80" fill="none" stroke="#fff" stroke-width="2.5"><path d="M42 4a14 14 0 0 1 14 14c0 12-14 26-14 26S28 30 28 18A14 14 0 0 1 42 4z"/><circle cx="42" cy="18" r="5"/><path d="M42 44v12M42 56L10 44M42 56L74 44M42 56L14 76M42 56L70 76"/></svg>
  <h3>ONLINE</h3><div class="sub">POSITIONING</div>
  <p>Online solution for brands to make merchandise available to their end customers</p>
  <span class="btn">LEARN MORE</span>
</div>
<div class="abs service green" style="left:703px">
  <svg width="96" height="74" viewBox="0 0 104 80" fill="none" stroke="#fff" stroke-width="2.5"><path d="M24 14h46v46H24zM70 30h18l12 16v14H70zM4 24h14M8 34h12M4 44h14"/><circle cx="40" cy="64" r="7"/><circle cx="84" cy="64" r="7"/></svg>
  <h3>LOGISTICS</h3><div class="sub">&amp; AFTERSALES</div>
  <p>Managing and executing loyalty programs that include coupon redemption,transaction</p>
  <span class="btn">LEARN MORE</span>
</div>
<div class="abs service teal" style="left:900px">
  <svg width="70" height="74" viewBox="0 0 76 80" fill="none" stroke="#fff" stroke-width="2.5"><path d="M6 30h64a32 24 0 0 1-64 0z"/><path d="M4 30h68M26 54L16 76M50 54l10 22M38 56v20M28 20c-4-5 4-9 0-14M38 20c-4-5 4-9 0-14M48 20c-4-5 4-9 0-14"/></svg>
  <h3>PROMOTIONAL</h3><div class="sub">BBQS</div>
  <p>Branded outdoor grills and leisure items that put your brand at every event</p>
  <span class="btn">LEARN MORE</span>
</div>

<section class="abs welcome">
  <div class="pre">Welcome to</div>
  <h2>Korvath Supply</h2>
  <p>We believe that the partners we work for should be able to focus on building their brand and product. Korvath Supply therefore takes care of the process from order processing to delivery. Together with our Partner Korvath Promotional, we can also provide support in commercial process. We have supplier relationships in more than 30 countries in both the retail and promotional products market. As experts in Outdoor Leisure Development from A to Z, we guide every product from first idea to delivery.</p>
  <span class="btn-solid">READ MORE</span>
</section>
<div class="abs accent-disc"></div>
<div class="abs photo-disc" role="img" aria-label="Photo of a port container crane at sunset"></div>

<section class="abs banner" role="img" aria-label="Photo of a loaded container ship in a harbour at dusk"></section>
<div class="abs banner-text">
  <div class="pre">Korvath Supply</div>
  <h2>Ensures Silent Distribution</h2>
  <p>Ensures the smooth distribution of promotional merchandise products for its customers. With our own warehouse and fleet, we are able to get products to the right place quickly and reliably, from small orders to larger, complex deliveries to multiple addresses.</p>
  <span class="btn-ghost">ASK FOR THE POSSIBILITIES</span>
</div>

<h2 class="abs blog-title">Latest <span>Blog</span></h2>
<div class="abs blog-rule"></div>

<article class="abs post" style="left:112px">
  <div class="thumb" role="img" aria-label="Photo of hands typing on a laptop" style="background:linear-gradient(135deg,#e9e4de,#b8b2ad)"></div>
  <div class="date">15 DEC 2021</div>
  <h3>SED UT PERSPICIATIS UNDE</h3>
  <p>Nemo enim ipsam voluptatem quia voluptas sit as pernatur aut odit aut fugit, sed quia consequ untur magni dolores eos qui ratione</p>
</article>
<article class="abs post" style="left:443px">
  <div class="thumb" role="img" aria-label="Photo of stacked shipping containers under blue light" style="background:linear-gradient(160deg,#1e3c9a,#6a4a3a 70%,#3a2a2a)"></div>
  <div class="date">15 DEC 2021</div>
  <h3>SED UT PERSPICIATIS UNDE</h3>
  <p>Nemo enim ipsam voluptatem quia voluptas sit as pernatur aut odit aut fugit, sed quia consequ untur magni dolores eos qui ratione</p>
</article>
<article class="abs post" style="left:775px">
  <div class="thumb" role="img" aria-label="Photo of a container terminal at night" style="background:linear-gradient(180deg,#5a6aa8,#2c3a6a 60%,#8a6a5a)"></div>
  <div class="date">15 DEC 2021</div>
  <h3>SED UT PERSPICIATIS UNDE</h3>
  <p>Nemo enim ipsam voluptatem quia voluptas sit as pernatur aut odit aut fugit, sed quia consequ untur magni dolores eos qui ratione</p>
</article>

<section class="abs partners"></section>
<div class="abs partner" style="left:112px">Smokehaven</div>
<div class="abs partner" style="left:310px">Emberline</div>
<div class="abs partner" style="left:510px">Caskfire</div>
<div class="abs partner" style="left:709px">Grillmont</div>
<div class="abs partner" style="left:908px">Korvath</div>

<footer class="abs site-footer"></footer>
<nav class="abs foot-nav"><span>HOME</span><span>ABOUT</span><span>CONTACT</span><span>OUR SERVICES</span><span>OUR NEWS</span></nav>
<div class="abs foot-rule"></div>

<h2 class="abs foot-h" style="left:112px">CONTACT US</h2>
<div class="abs field" style="left:112px;top:3303px;width:181px;height:37px">First Name :</div>
<div class="abs field" style="left:302px;top:3303px;width:181px;height:37px">Last Name :</div>
<div class="abs field" style="left:112px;top:3348px;width:181px;height:37px">Email :</div>
<div class="abs field" style="left:302px;top:3348px;width:181px;height:37px">Phone :</div>
<div class="abs field" style="left:112px;top:3393px;width:371px;height:54px">Message :</div>
<div class="abs submit">SUBMIT</div>

<h2 class="abs foot-h" style="left:561px">ADDRESS</h2>
<div class="abs contact-item" style="top:3306px">
  <span class="ic"><svg width="14" height="20" viewBox="0 0 14 20"><path d="M7 0a7 7 0 0 1 7 7c0 5-7 13-7 13S0 12 0 7a7 7 0 0 1 7-7z" fill="#fff"/><circle cx="7" cy="7" r="2.5" fill="#325f6c"/></svg></span>
  <div><b>ADDRESS</b><span>Lindenkade 12,<br>4811 KV Ridderveld</span></div>
</div>
<div class="abs contact-item" style="top:3382px">
  <span class="ic"><svg width="18" height="18" viewBox="0 0 24 24"><path d="M6.6 10.8a15 15 0 0 0 6.6 6.6l2.2-2.2c.3-.3.7-.4 1-.2 1.1.4 2.3.6 3.6.6.6 0 1 .4 1 1V20c0 .6-.4 1-1 1A17 17 0 0 1 3 4c0-.6.4-1 1-1h3.5c.6 0 1 .4 1 1 0 1.3.2 2.5.6 3.6.1.3 0 .7-.2 1z" fill="#fff"/></svg></span>
  <div><b>PHONE</b><span>+31 (010) 555 0142</span></div>
</div>
<div class="abs contact-item" style="top:3446px">
  <span class="ic"><svg width="18" height="14" viewBox="0 0 18 14"><rect width="18" height="14" rx="1" fill="#fff"/><path d="M1 1l8 6 8-6" stroke="#325f6c" stroke-width="1.6" fill="none"/></svg></span>
  <div><b>EMAIL</b><span>info@korvathsupply.example</span></div>
</div>

<div class="abs foot-brand"><span class="dot"></span>KORVATH</div>
<span class="abs social" style="left:850px"></span>
<span class="abs social" style="left:893px"></span>
<span class="abs social" style="left:936px"></span>
<span class="abs social" style="left:979px"></span>
<span class="abs social" style="left:1022px"></span>

<p class="abs copyright">© Copyright 2021 Korvath Supply.All Rights Reserved</p>

</body>
</html>
```